Card design for orthopaedic surgeons working as The Brightwater Joint Centre

Business cards, letterhead

Colors

Designer to choose colors to be used in the design.

Requirements
Must have
• Late addition.
• Cards letterhead must have logos of
• Crestmoor Lindell College of Surgeons
• Varenwood Bone Health Association
Nice to have
• Back of card to have space for appointment time to be added by hand and some blank space for writing incidental other notes.

```html
<!DOCTYPE html>
<html lang="en">
<head>
<meta charset="utf-8">
<title>The Brightwater Joint Centre — Stationery</title>
<link rel="stylesheet" href="https://fonts.googleapis.com/css2?family=Questrial&family=Open+Sans:ital,wght@0,400;0,600;1,400&display=swap">
<style>
:root{
  --backdrop:#dcdcdc;
  --paper:#ffffff;
  --brand-blue:#2eaaf5;
  --brand-navy:#0f2d45;
  --ink:#3f4a54;
  --ink-soft:#5c6670;
  --dots:#8a97a3;
}
*{box-sizing:border-box;margin:0;padding:0}
html,body{width:1200px;height:877px;overflow:hidden;background:var(--backdrop)}
body{position:relative;font-family:"Questrial",sans-serif;color:var(--ink)}

.card{position:absolute;left:118px;width:368px;height:210px;background:var(--paper);border-radius:14px;overflow:hidden;box-shadow:0 1px 3px rgba(0,0,0,.12)}
.card--front{top:271px}
.card--back{top:530px}

.contact-panel{position:absolute;left:196px;right:0;top:92px;bottom:0;background:var(--brand-blue)}
.base-rule{position:absolute;left:0;right:0;bottom:0;height:8px;background:var(--brand-navy)}

.brand{position:absolute;font-family:"Questrial",sans-serif;color:var(--brand-navy);white-space:nowrap;letter-spacing:-.2px}
.card--front .brand{left:22px;top:46px;font-size:15px}
.card--back .brand{left:0;right:0;top:25px;text-align:center;font-size:15px}

.holder{position:absolute;left:30px;width:130px;top:90px;text-align:center}
.holder__name{font-family:"Open Sans",sans-serif;font-weight:600;font-size:13.5px;color:var(--brand-blue)}
.holder__role{font-family:"Open Sans",sans-serif;font-size:8.5px;color:var(--brand-navy);margin-top:-2px}

.card-contact{position:absolute;right:22px;top:106px;text-align:right;color:#fff;font-size:9px;line-height:10.5px}
.card-contact .gap{height:6px}
.card-contact .row{display:flex;justify-content:flex-end;align-items:center;gap:4px}
.icon{width:7px;height:7px;flex:none}

.form{position:absolute;left:22px;right:22px;font-size:11px;color:var(--brand-blue);display:flex;align-items:flex-end;gap:3px}
.form .fill{flex:1;border-bottom:1px dotted var(--dots);height:1px;margin-bottom:3px}
.form small{font-size:8px;margin-left:2px}
.days{position:absolute;left:24px;right:22px;top:106px;display:flex;justify-content:space-between;font-size:9.5px;color:var(--brand-blue)}
.days span{display:flex;align-items:center;gap:5px}
.days i{display:inline-block;width:10px;height:8px;border:1.3px solid var(--brand-navy)}
.blank-line{position:absolute;left:22px;right:22px;top:159px;border-bottom:1px dotted var(--dots)}
.policy{position:absolute;left:40px;right:40px;top:176px;text-align:center;font-family:"Open Sans",sans-serif;font-style:italic;font-size:7.6px;line-height:10.5px;color:var(--ink)}

.letterhead{position:absolute;left:557px;top:69px;width:527px;height:742px;background:var(--paper);box-shadow:0 1px 3px rgba(0,0,0,.12)}
.letterhead .brand{left:46px;top:66px;font-size:13px}
.sender{position:absolute;left:349px;top:32px;font-size:7.6px;line-height:9.7px;color:var(--ink-soft);letter-spacing:.3px}
.sender .row{display:flex;align-items:center;gap:5px}
.sender .icon{width:6px;height:6px}
.salutation{position:absolute;left:46px;top:206px;font-size:13.5px;color:var(--ink)}
.letter-body{position:absolute;left:46px;top:248px;width:438px;font-size:7.9px;line-height:11.4px;color:var(--ink);text-align:justify}
.letter-body p{margin-bottom:11.4px}
.closing{position:absolute;left:46px;top:486px;font-size:7.6px;color:var(--ink)}
.signature-area{position:absolute;left:46px;top:516px;width:60px;height:30px;background:#eef1f4;border-radius:2px}
</style>
</head>
<body>

<section class="card card--front" aria-label="Business card front">
  <div class="contact-panel"></div>
  <div class="base-rule"></div>
  <div class="brand">The Brightwater Joint Centre</div>
  <div class="holder">
    <div class="holder__name">Daniel Harrow</div>
    <div class="holder__role">President</div>
  </div>
  <div class="card-contact">
    <div>412 Fernhollow Road</div>
    <div>Kelsmere, Oregon 97481</div>
    <div class="gap"></div>
    <div class="row">555-014-2286 <svg class="icon" viewBox="0 0 10 10"><path d="M2 0.5 L4 3 L3 4.2 Q4.5 6.2 5.8 7 L7 5.8 L9.5 8 L8 9.5 Q3.5 9 0.5 2 Z" fill="#fff"/></svg></div>
    <div class="row">555-017-3390 <svg class="icon" viewBox="0 0 10 10"><rect x="2.5" y="0.5" width="5" height="9" rx="1" fill="none" stroke="#fff" stroke-width="1.2"/></svg></div>
    <div class="row">555-019-4472 <svg class="icon" viewBox="0 0 10 10"><rect x="2.5" y="1" width="5" height="3" fill="#fff"/><rect x="0.5" y="4" width="9" height="5" fill="#fff"/></svg></div>
    <div class="row">daniel@brightwaterjoint.com <svg class="icon" viewBox="0 0 10 10"><rect x="0.5" y="2" width="9" height="6" fill="#fff"/><path d="M0.5 2 L5 5.5 L9.5 2" stroke="var(--brand-blue)" fill="none"/></svg></div>
    <div class="row">www.brightwaterjoint.com <svg class="icon" viewBox="0 0 10 10"><circle cx="5" cy="5" r="4.5" fill="#fff"/><path d="M1 5 H9 M5 1 V9" stroke="var(--brand-blue)"/></svg></div>
  </div>
</section>

<section class="card card--back" aria-label="Business card back, appointment card">
  <div class="brand">The Brightwater Joint Centre</div>
  <div class="form" style="top:55px">Name :<span class="fill"></span></div>
  <div class="form" style="top:77px">Date :<span class="fill" style="flex:0 0 145px"></span><span style="margin-left:2px">Time :</span><span class="fill"></span><small>AM/PM</small></div>
  <div class="days">
    <span>Sun <i></i></span><span>Mon <i></i></span><span>Tue <i></i></span><span>Wed <i></i></span><span>Thu <i></i></span><span>Fri <i></i></span><span>Sat <i></i></span>
  </div>
  <div class="form" style="top:126px">Note :<span class="fill"></span></div>
  <div class="blank-line"></div>
  <p class="policy">Please give me 24 hours notice if you are unable to keep your appointment or a cancellation fee may be charged.</p>
</section>

<section class="letterhead" aria-label="Letterhead">
  <div class="brand">The Brightwater Joint Centre</div>
  <div class="sender">
    <div>412 Fernhollow Road</div>
    <div>Kelsmere, Oregon 97481</div>
    <div class="row"><svg class="icon" viewBox="0 0 10 10"><path d="M2 0.5 L4 3 L3 4.2 Q4.5 6.2 5.8 7 L7 5.8 L9.5 8 L8 9.5 Q3.5 9 0.5 2 Z" fill="var(--brand-blue)"/></svg>555-014-2286</div>
    <div class="row"><svg class="icon" viewBox="0 0 10 10"><rect x="2.5" y="0.5" width="5" height="9" rx="1" fill="none" stroke="var(--brand-blue)" stroke-width="1.4"/></svg>555-017-3390</div>
    <div class="row"><svg class="icon" viewBox="0 0 10 10"><rect x="2.5" y="1" width="5" height="3" fill="var(--brand-blue)"/><rect x="0.5" y="4" width="9" height="5" fill="var(--brand-blue)"/></svg>555-019-4472</div>
    <div class="row"><svg class="icon" viewBox="0 0 10 10"><rect x="0.5" y="2" width="9" height="6" fill="var(--brand-blue)"/><path d="M0.5 2 L5 5.5 L9.5 2" stroke="#fff" fill="none"/></svg>daniel@brightwaterjoint.com</div>
    <div class="row"><svg class="icon" viewBox="0 0 10 10"><circle cx="5" cy="5" r="4.5" fill="var(--brand-blue)"/><path d="M1 5 H9 M5 1 V9" stroke="#fff"/></svg>www.brightwaterjoint.com</div>
  </div>

  <p class="salutation">Dear Mr. Harrow,</p>
  <div class="letter-body">
    <p>Lorem ipsum dolor sit amet, consectetur adipiscing elit. Donec orci purus, luctus vitae dignissim eu, iaculis sed purus. Vivamus faucibus, ipsum nec aliquet viverra, leo mauris condimentum ligula, sit amet sagittis enim ligula quis arcu. Nam egestas tortor id nisi porttitor mattis. In tortor ante, ultricies in suscipit a, tempus non massa. Vivamus et auctor mi. Fusce vel massa nulla. Phasellus nec eros mauris, et scelerisque orci.</p>
    <p>Donec malesuada orci vitae nulla accumsan porta a id massa. Quisque accumsan iaculis magna sit amet fringilla. Maecenas consequat, magna eget tincidunt semper, odio nibh rutrum mi, id feugiat ante nisi eu risus. Vestibulum nunc orci, rhoncus a placerat in, ultricies in mi. Cras mattis varius eros, vel fringilla nisi suscipit eget. Quisque scelerisque sagittis nulla at porttitor.</p>
    <p>Sed id augue vitae urna euismod commodo aliquet a quam. Pellentesque arcu velit, cursus et malesuada ut, consequat et diam. Nullam erat sem, rhoncus id ullamcorper vitae, rhoncus et arcu. In ultricies ultricies nulla, ut rutrum nisi iaculis at. Donec eu magna a metus ornare faucibus. Fusce aliquet faucibus ultricies. Morbi semper, est id tincidunt gravida, sem arcu adipiscing lacus, ac bibendum nulla leo eu purus. Quisque nec diam sed risus consectetur a ccumsan quis quis nibh. Vestibulum id purus lorem.</p>
    <p>It is a long established fact that a reader will be distracted by the readable content of a page when looking at its layout. The point of using Lorem Ipsum is that it has a more-or-less normal distribution of letters, as opposed to using 'Content here, content here', making it look like readable English. Many desktop publishing packages</p>
  </div>
  <p class="closing">Sincerely,</p>
  <div class="signature-area" role="img" aria-label="Handwritten signature of the sender"></div>
</section>

</body>
</html>
```